Verlindo Magician

I want the business card for my business to give to people who watch that later I will be employed to show magic here is my website http://www.verlindoillusions.example/I want the interesting design , i am very opened for formal and informal, I watch a lot of design so don't stick to the common shape and form but i hope it can also be produced the thing to write on will be the same as in picture that i will upload , i also will upload the logo for you that so can be easy to useDenis CostilleMagicianMAGICIAN BALSAMO 17 rue des Tilleuls - 25000 BESANÇON contact@verlindoillusions.example tel. 0381 946 157 tel. 0674 219 503

```html
<!DOCTYPE html>
<html lang="fr">
<head>
<meta charset="utf-8">
<title>Verlindo Magician – Business Card</title>
<link rel="stylesheet" href="https://fonts.googleapis.com/css2?family=Montserrat:wght@300;400;600&display=swap">
<style>
  :root {
    --backdrop: #2b2d31;
    --card-white: #ffffff;
    --card-black: #0b0b0c;
    --ink: #111111;
    --ink-soft: #3a3a3a;
    --illustration: #1a1a1a;
    --illustration-light: #d9d9d9;
    --accent-red: #c4161c;
  }
  * { box-sizing: border-box; margin: 0; padding: 0; }
  html, body {
    width: 1200px; height: 900px; overflow: hidden;
    background: var(--backdrop);
    font-family: "Montserrat", sans-serif;
  }
  .stage {
    width: 1200px; height: 900px;
    display: flex; align-items: center; justify-content: center; gap: 110px;
  }
  .card {
    width: 360px; height: 580px;
    border-radius: 30px;
    position: relative;
  }
  /* Front */
  .card--front {
    background: var(--card-white);
    color: var(--ink);
    padding: 64px 44px 0 52px;
  }
  .portrait {
    display: block;
    width: 170px; height: 150px;
    margin-left: 36px;
    border-radius: 6px;
    background: linear-gradient(160deg, var(--illustration) 0%, #3c3c3c 100%);
  }
  .brand-name {
    margin: 14px 0 0 60px;
    font-weight: 300;
    font-size: 32px;
    letter-spacing: 1px;
    line-height: 1;
  }
  .brand-sub {
    margin: 4px 0 0 96px;
    font-weight: 300;
    font-size: 9px;
    letter-spacing: 2px;
    color: var(--ink-soft);
  }
  .person { margin-top: 30px; }
  .person__name {
    font-weight: 600;
    font-size: 27px;
    letter-spacing: 0.5px;
    line-height: 1;
  }
  .person__role {
    margin-top: 4px;
    padding-left: 100px;
    font-weight: 300;
    font-size: 14px;
    letter-spacing: 1px;
  }
  .address {
    margin-top: 26px;
    display: flex; align-items: center; gap: 16px;
  }
  .address__icon { width: 24px; height: 32px; flex: none; }
  .address__text {
    font-weight: 400;
    font-size: 16px;
    line-height: 1.1;
    letter-spacing: 0.5px;
  }
  .contact {
    margin-top: 34px;
    list-style: none;
    font-weight: 300;
    font-size: 12.5px;
    line-height: 1.55;
    letter-spacing: 0.6px;
  }
  /* Back */
  .card--back {
    background: var(--card-black);
    display: flex; align-items: center; justify-content: center;
  }
  .seal {
    width: 250px; height: 250px;
    border-radius: 50%;
    background: var(--card-white);
    display: flex; flex-direction: column; align-items: center; justify-content: center;
  }
  .seal .portrait-small {
    width: 120px; height: 110px;
    border-radius: 6px;
    background: linear-gradient(160deg, var(--illustration) 0%, #3c3c3c 100%);
  }
  .seal .brand-name {
    margin: 10px 0 0 0;
    font-size: 22px;
    color: var(--ink);
  }
  .seal .brand-sub { margin: 3px 0 0 0; font-size: 7px; }
</style>
</head>
<body>
<main class="stage">
  <section class="card card--front" aria-label="Card front">
    <div class="portrait" role="img" aria-label="Black and white illustration of the magician holding playing cards"></div>
    <p class="brand-name">VERLINDO</p>
    <p class="brand-sub">MAGICIEN</p>

    <div class="person">
      <h1 class="person__name">MARC RAVOULET</h1>
      <p class="person__role">MAGICIAN</p>
    </div>

    <div class="address">
      <svg class="address__icon" viewBox="0 0 24 32" aria-hidden="true">
        <path d="M12 1C6.5 1 2 5.3 2 10.8 2 18 12 27 12 27s10-9 10-16.2C22 5.3 17.5 1 12 1z" fill="var(--ink)"/>
        <circle cx="12" cy="10.5" r="4" fill="var(--card-white)"/>
        <path d="M5 27.5c0 2 3.2 3 7 3s7-1 7-3" fill="none" stroke="var(--ink)" stroke-width="2" stroke-linecap="round"/>
      </svg>
      <p class="address__text">17 RUE DES TILLEULS<br>25000 BESANÇON</p>
    </div>

    <ul class="contact">
      <li>CONTACT@VERLINDOILLUSIONS.EXAMPLE</li>
      <li>0381 946 157/0674 219 503</li>
      <li>WWW.VERLINDOILLUSIONS.EXAMPLE</li>
    </ul>
  </section>

  <section class="card card--back" aria-label="Card back">
    <div class="seal">
      <div class="portrait-small" role="img" aria-label="Black and white illustration of the magician holding playing cards"></div>
      <p class="brand-name">VERLINDO</p>
      <p class="brand-sub">MAGICIEN</p>
    </div>
  </section>
</main>
</body>
</html>
```